UI/ UX Design for ERP Software

We need a new UX/UI interface for a ERP software for property managers. Our CMMS / ERP solution is made based on responsive design technologies and is coded in PHP.
The overall UX to be similar to Tev Ulna - easy navigation, intuitive menus.

Industry/Entity Type

Property Management

Number of Pages Required

5+ page

Requirements
Must have
• Round dock buttons
Consistent icons across the application
Enough Spacing between buttons/icons/ menu
Consistent Font
Nice to have
• We would like the UX to allow the users to use the application without /minimum training.
Should not have
• we don't want anything that is classic with respect to UX

```html
<!DOCTYPE html>
<html lang="en">
<head>
<meta charset="utf-8">
<title>Domora – Dashboard</title>
<link rel="stylesheet" href="https://fonts.googleapis.com/css2?family=Lato:wght@400;700&display=swap">
<style>
:root{
  --brand:#1a8cff;
  --page:#eaf1fb;
  --panel:#ffffff;
  --ink:#1f2a3a;
  --muted:#7d8795;
  --nav-ink:#3d5a80;
  --nav-active:#e2ecfa;
  --line:#e6e9ee;
  --pink:#f45fa8;
  --online:#3ddc84;
}
*{box-sizing:border-box;margin:0;padding:0}
html,body{width:1200px;height:1018px;overflow:hidden}
body{font-family:'Lato',sans-serif;background:var(--page);color:var(--ink);position:relative}
.sidebar{position:absolute;left:0;top:0;width:258px;height:1018px;background:#fff}
.brand{height:68px;background:var(--brand);display:flex;align-items:center;padding-left:34px;gap:8px}
.brand-mark{width:14px;height:14px;border-radius:50%;background:#fff}
.brand-name{color:#fff;font-size:27px;font-weight:700}
.nav-label{font-size:10px;color:var(--muted);letter-spacing:.3px;padding:13px 0 0 26px;height:33px}
.nav{list-style:none}
.nav li{height:37.6px;display:flex;align-items:center;padding-left:25px;gap:10px;font-size:16px;color:var(--nav-ink)}
.nav li.active{background:var(--nav-active);border-right:2px solid var(--brand);color:var(--nav-ink)}
.nav svg{width:20px;height:20px;fill:none;stroke:#333;stroke-width:1.4}
.nav li.active svg{stroke:var(--brand)}
.topbar{position:absolute;left:258px;top:0;right:0;height:68px;background:#fff}
.search{position:absolute;left:30px;top:15px;width:231px;height:38px;background:#f1f2f4;display:flex;align-items:center;padding-left:14px;gap:7px;font-size:11px;color:var(--muted)}
.top-icons{position:absolute;right:28px;top:13px;display:flex;align-items:center;gap:14px}
.dot-icon{position:relative;width:26px;height:26px}
.dot-icon i{position:absolute;right:0;top:0;width:7px;height:7px;border-radius:50%;background:#ec4c8a}
.avatar-sm{width:40px;height:40px;border-radius:50%;background:radial-gradient(circle at 50% 40%,#c9a28a,#5b4537)}
.user-name{font-size:14px;color:var(--ink);display:flex;align-items:center;gap:5px;margin-right:18px}
.page-head{position:absolute;left:293px;top:84px}
.page-head h1{font-size:19px;font-weight:400;color:var(--ink)}
.page-head p{font-size:11px;color:var(--muted);margin-top:3px}
.range-label{position:absolute;left:923px;top:97px;font-size:12px;color:var(--nav-ink)}
.range{position:absolute;left:995px;top:87px;width:177px;height:36px;background:#fff;display:flex;align-items:center;justify-content:space-between;padding:0 10px;font-size:10.5px;color:var(--ink)}
.stat{position:absolute;top:144px;height:66px;color:#fff;display:flex;align-items:center;padding-left:18px;gap:10px}
.stat svg{width:34px;height:34px;fill:none;stroke:#fff;stroke-width:1.4;flex:none}
.stat .k{font-size:11px;text-transform:uppercase}
.stat .v{font-size:15.5px;margin-top:1px}
.s1{left:283px;width:143px;background:linear-gradient(90deg,#f06fc6,#f38bd4)}
.s2{left:433px;width:143px;background:linear-gradient(90deg,#f6934c,#f7a15a)}
.s3{left:583px;width:210px;background:linear-gradient(90deg,#9a5cf1,#b479f3)}
.s4{left:800px;width:186px;background:linear-gradient(90deg,#22c8a0,#36e08f)}
.s5{left:993px;width:187px;background:#12b0f5}
.chart{position:absolute;left:287px;top:218px;width:893px;height:392px;background:var(--panel)}
.periods{position:absolute;right:18px;top:12px;display:flex;gap:12px;font-size:11.5px;color:var(--ink)}
.periods span{display:flex;align-items:center;gap:6px}
.periods b{width:10px;height:10px;border-radius:50%;border:1px solid #b9c0c9;font-weight:400}
.periods b.on{border:none;background:var(--brand)}
.chart svg{position:absolute;left:0;top:0}
.axis{font-size:11.5px;fill:var(--ink);font-family:'Lato',sans-serif}
.donut-panel{position:absolute;left:290px;top:663px;width:447px;height:279px;background:var(--panel)}
.donut-panel svg{position:absolute;left:22px;top:42px}
.legend{position:absolute;left:228px;top:28px;list-style:none}
.legend li{height:33.6px;display:flex;align-items:center;gap:7px;font-size:11.5px;color:#111}
.legend i{width:9px;height:9px;border-radius:50%}
.users-title{position:absolute;left:767px;top:635px;font-size:16px;color:var(--ink)}
.users-note{position:absolute;right:33px;top:639px;font-size:12.5px;color:var(--muted)}
.users{position:absolute;left:764px;top:663px;width:414px;height:279px;background:var(--panel);list-style:none;padding-top:17px}
.users li{height:65.5px;display:flex;align-items:center;padding-left:17px;position:relative}
.users .photo{width:54px;height:48px;border-radius:12px;background:linear-gradient(135deg,#8d7868,#3f4a55)}
.users .who{margin-left:14px}
.users .who strong{display:block;font-size:15.5px;font-weight:400;color:var(--ink)}
.users .who small{font-size:11.5px;color:var(--muted)}
.users .status{position:absolute;right:18px;top:13px;width:77px;height:28px;border-radius:14px;background:#fff;box-shadow:0 2px 8px rgba(0,0,0,.06);color:var(--online);font-size:14px;display:flex;align-items:center;justify-content:center}
</style>
</head>
<body>
<aside class="sidebar">
  <div class="brand"><span class="brand-mark"></span><span class="brand-name">Domora</span></div>
  <div class="nav-label">NAVIGATIONS</div>
  <ul class="nav">
    <li class="active"><svg viewBox="0 0 20 20"><path d="M3 14a7 7 0 1 1 14 0"/><path d="M10 14l4-5"/></svg>Dashboard</li>
    <li><svg viewBox="0 0 20 20"><circle cx="6" cy="7" r="2.3"/><circle cx="14" cy="7" r="2.3"/><circle cx="10" cy="5" r="2"/><path d="M2 16c0-3 2-5 4-5s4 2 4 5M10 16c0-3 2-5 4-5s4 2 4 5"/></svg>Customers</li>
    <li><svg viewBox="0 0 20 20"><path d="M3 10l7-6 7 6M5 8.5V17h10V8.5M8.5 17v-4h3v4"/></svg>Properties</li>
    <li><svg viewBox="0 0 20 20"><circle cx="11" cy="5" r="2.5"/><path d="M11 7.5v5M3 17h14M6 14l5-1.5 4 1.5"/></svg>Tenants</li>
    <li><svg viewBox="0 0 20 20"><rect x="3" y="5" width="14" height="10" rx="1"/><path d="M3 6l7 5 7-5"/></svg>Contacts</li>
    <li><svg viewBox="0 0 20 20"><circle cx="10" cy="6" r="3"/><path d="M6 3.5h8M5 18v-4a5 5 0 0 1 10 0v4"/></svg>Contractors</li>
    <li><svg viewBox="0 0 20 20"><circle cx="5" cy="9" r="2"/><circle cx="10" cy="6" r="2"/><circle cx="15" cy="9" r="2"/><path d="M1 17c0-3 2-5 4-5M19 17c0-3-2-5-4-5M6 17c0-4 2-7 4-7s4 3 4 7"/></svg>Employees</li>
    <li><svg viewBox="0 0 20 20"><circle cx="10" cy="10" r="3"/><circle cx="10" cy="10" r="7" stroke-dasharray="2 2"/></svg>Compliance Management</li>
    <li><svg viewBox="0 0 20 20"><circle cx="10" cy="10" r="7" stroke-dasharray="3 1.5"/><circle cx="10" cy="10" r="3"/></svg>Prevent. Maintenance</li>
    <li><svg viewBox="0 0 20 20"><rect x="4" y="2.5" width="12" height="15" rx="1"/><path d="M7 7h6M7 10h6M7 13h4"/></svg>Work Orders</li>
    <li><svg viewBox="0 0 20 20"><rect x="3" y="4" width="14" height="13"/><path d="M6 8h8M6 11h8M6 14h5M7 2v3M13 2v3"/></svg>Purchase Orders</li>
    <li><svg viewBox="0 0 20 20"><path d="M3 9l7-6 7 6v8H3z"/><circle cx="10" cy="11" r="2.5"/><path d="M12 13l3 3"/></svg>Property Inspections</li>
    <li><svg viewBox="0 0 20 20"><path d="M12 2L6 11h4l-2 7 6-9h-4z"/></svg>Energy Management</li>
    <li><svg viewBox="0 0 20 20"><path d="M10 3l7 13H3z"/><path d="M10 8v4M10 14v.5"/></svg>Risk Management</li>
    <li><svg viewBox="0 0 20 20"><rect x="4" y="2.5" width="12" height="15" rx="1"/><path d="M7 7l2 2 4-4M7 13h6"/></svg>Project Management</li>
    <li><svg viewBox="0 0 20 20"><ellipse cx="8" cy="5" rx="5" ry="2"/><path d="M3 5v8c0 1 2 2 5 2M13 5v3"/><circle cx="14" cy="13" r="3.5"/></svg>Financial - Budgeting</li>
    <li><svg viewBox="0 0 20 20"><rect x="3" y="6" width="14" height="11"/><path d="M3 7l7 5 7-5M10 2v6"/></svg>Tenant Requests</li>
    <li><svg viewBox="0 0 20 20"><rect x="4" y="2.5" width="12" height="15" rx="1"/><path d="M7 6h6M7 9h6M7 12h6M7 15h3"/></svg>Reports</li>
    <li><svg viewBox="0 0 20 20"><path d="M3 17h14M5 17v-5M9 17V9M13 17v-7M17 17V5M4 9l5-4 4 3 4-4"/></svg>Visual Reports</li>
    <li><svg viewBox="0 0 20 20"><path d="M2 5h6l2 2h8v10H2z"/></svg>Files</li>
    <li><svg viewBox="0 0 20 20"><rect x="3" y="3" width="10" height="14" rx="1"/><path d="M13 5h3v12h-9"/></svg>Pages</li>
    <li><svg viewBox="0 0 20 20"><circle cx="10" cy="10" r="6" stroke-dasharray="3 1.5"/><circle cx="10" cy="10" r="2.5"/></svg>Configurations</li>
    <li><svg viewBox="0 0 20 20"><path d="M2 5h16M2 10h16M2 15h16"/><circle cx="7" cy="5" r="1.5"/><circle cx="13" cy="10" r="1.5"/><circle cx="6" cy="15" r="1.5"/></svg>Settings</li>
  </ul>
</aside>

<header class="topbar">
  <div class="search"><svg width="12" height="12" viewBox="0 0 12 12" fill="none" stroke="#555" stroke-width="1.6"><circle cx="5" cy="5" r="3.8"/><path d="M8 8l3 3"/></svg>Search...</div>
  <div class="top-icons">
    <div class="dot-icon"><svg width="24" height="26" viewBox="0 0 24 26" fill="none" stroke="#2a3a55" stroke-width="1.8"><rect x="1" y="8" width="22" height="15"/><path d="M1 9l11 8 11-8M1 23l8-7M23 23l-8-7"/></svg><i></i></div>
    <div class="dot-icon"><svg width="24" height="26" viewBox="0 0 24 26" fill="#2a3a55"><path d="M12 4c-4 0-6 3-6 7v6l-2 3h16l-2-3v-6c0-4-2-7-6-7z"/><circle cx="12" cy="22.5" r="2"/></svg><i></i></div>
    <div class="avatar-sm" role="img" aria-label="Profile photo of the signed-in user"></div>
    <div class="user-name">Arlo Penn <svg width="9" height="6" viewBox="0 0 9 6"><path d="M0 0h9L4.5 6z" fill="#2a3a55"/></svg></div>
    <svg width="20" height="14" viewBox="0 0 20 14" fill="none" stroke="#2a3a55" stroke-width="2"><path d="M0 1h20M0 7h20M0 13h20"/></svg>
  </div>
</header>

<div class="page-head"><h1>Dashboard</h1><p>Welcome to Domora</p></div>
<div class="range-label">Date Range</div>
<div class="range">19-09-2020 &nbsp;- &nbsp;19-01 -2021
  <svg width="14" height="14" viewBox="0 0 14 14" fill="none" stroke="#555" stroke-width="1"><rect x="1" y="2" width="12" height="11"/><path d="M1 5h12M4 0v3M10 0v3M3 7h2M6 7h2M9 7h2M3 10h2M6 10h2M9 10h2"/></svg></div>

<div class="stat s1"><svg viewBox="0 0 34 34"><path d="M4 31V8h10v23M14 31V13h14v18M2 31h30M7 12h4M7 16h4M7 20h4M7 24h4M17 17h3M22 17h3M17 21h3M22 21h3M17 25h3M22 25h3"/></svg><div><div class="k">Properties</div><div class="v">03</div></div></div>
<div class="stat s2"><svg viewBox="0 0 34 34"><circle cx="19" cy="7" r="4"/><path d="M19 11v12M19 16h3M19 20h3M3 30l7-3h8l7-4M3 26l5-2h6"/></svg><div><div class="k">Tenants</div><div class="v">08</div></div></div>
<div class="stat s3"><svg viewBox="0 0 34 34"><path d="M3 31V12l7-5 7 5v19M17 31V8h14v23M1 31h32M6 16h2M11 16h2M6 21h2M11 21h2M21 12h2M26 12h2M21 17h2M26 17h2M21 22h2M26 22h2"/></svg><div><div class="k">Total Properties Area</div><div class="v">422,000.00sq.ft.</div></div></div>
<div class="stat s4"><svg viewBox="0 0 34 34"><path d="M3 14L17 4l14 10M6 12v19h22V12"/><rect x="9" y="17" width="16" height="7"/><circle cx="17" cy="10" r="2"/></svg><div><div class="k">Rented Area</div><div class="v">233,500.00sq.ft.</div></div></div>
<div class="stat s5"><svg viewBox="0 0 34 34"><path d="M5 31V6h12v25M17 31V12h12v19M2 31h30M8 10h2M12 10h2M8 15h2M12 15h2M8 20h2M12 20h2M21 16h2M25 16h2M21 21h2M25 21h2M21 26h2M25 26h2"/></svg><div><div class="k">Vacancies Area</div><div class="v">188,500.00sq.ft</div></div></div>

<section class="chart">
  <svg width="893" height="392" viewBox="0 0 893 392">
    <g stroke="#eceef2" stroke-width="1">
      <path d="M39 63V331M144 63V331M250 63V331M356 63V331M462 63V331M568 63V331M674 63V331M780 63V331M887 63V331"/>
      <path d="M39 331H887M39 282.5H887M39 234H887M39 185.5H887M39 137H887M39 88.5H887"/>
    </g>
    <g class="axis" text-anchor="end">
      <text x="35" y="335">0</text><text x="35" y="286">0.25</text><text x="35" y="238">0.5</text>
      <text x="35" y="189">0.75</text><text x="35" y="141">1</text><text x="35" y="92">1.25</text>
    </g>
    <g class="axis" text-anchor="middle">
      <text x="144" y="347">27Dec</text><text x="144" y="361">2020</text>
      <text x="253" y="347">28Dec</text><text x="253" y="361">2020</text>
      <text x="359" y="347">29Dec</text><text x="359" y="361">2020</text>
      <text x="467" y="347">30Dec</text><text x="467" y="361">2020</text>
      <text x="572" y="347">31Dec</text><text x="572" y="361">2020</text>
      <text x="677" y="347">01Jan</text><text x="677" y="361">2021</text>
      <text x="786" y="347">02Jan</text><text x="786" y="361">2021</text>
    </g>
    <path d="M41 331C70 318 85 312 100 312C120 312 140 288 170 284C200 280 225 262 250 261C268 260 282 248 294 236C315 214 335 192 356 186C390 176 420 138 464 138C500 144 530 150 580 130C640 108 690 93 744 81" fill="none" stroke="var(--pink)" stroke-width="1.8"/>
    <g fill="var(--pink)">
      <circle cx="41" cy="331" r="4.5"/><circle cx="170" cy="284" r="4.5"/><circle cx="250" cy="261" r="4.5"/>
      <circle cx="294" cy="236" r="4.5"/><circle cx="356" cy="186" r="4.5"/><circle cx="464" cy="138" r="4.5"/>
    </g>
  </svg>
  <div class="periods">
    <span><b class="on"></b>Last 7 days</span><span><b></b>Last months</span><span><b></b>Last 7 months</span>
    <span><b></b>Next 7 days</span><span><b></b>Next months</span><span><b></b>Next 3 months</span>
  </div>
</section>

<section class="donut-panel">
  <svg width="182" height="182" viewBox="0 0 182 182" fill="none" stroke-width="18">
    <g transform="translate(91 91)">
      <circle r="81" stroke="#8079e8" stroke-dasharray="42.4 466.5" transform="rotate(200)"/>
      <circle r="81" stroke="#3d3b44" stroke-dasharray="99 410" transform="rotate(230)"/>
      <circle r="81" stroke="#f5a25a" stroke-dasharray="169.6 339.3" transform="rotate(-60)"/>
      <circle r="81" stroke="#e4d650" stroke-dasharray="63.6 445.3" transform="rotate(60)"/>
      <circle r="81" stroke="#8ce874" stroke-dasharray="46.7 462.2" transform="rotate(105)"/>
      <circle r="81" stroke="#ef5a7c" stroke-dasharray="48 460.9" transform="rotate(138)"/>
      <circle r="81" stroke="#7ab2ec" stroke-dasharray="39.6 469.3" transform="rotate(172)"/>
    </g>
  </svg>
  <ul class="legend">
    <li><i style="background:#7ab2ec"></i>Scheduled Maintenance</li>
    <li><i style="background:#8ce874"></i>Completed Scheduled Maintenance</li>
    <li><i style="background:#f5a25a"></i>Future Scheduled Maintenance</li>
    <li><i style="background:#3d3b44"></i>Scheduled Work Orders</li>
    <li><i style="background:#8079e8"></i>Completed Work Orders</li>
    <li><i style="background:#ef5a7c"></i>Property Injections In Progress</li>
    <li><i style="background:#e4d650"></i>Completed Property Injections</li>
  </ul>
</section>

<h2 class="users-title">Users</h2>
<div class="users-note">last 24 hours</div>
<ul class="users">
  <li><div class="photo" role="img" aria-label="User profile photo"></div><div class="who"><strong>Rhys Calder</strong><small>Lorem Ipsum</small></div><span class="status">Online</span></li>
  <li><div class="photo" role="img" aria-label="User profile photo"></div><div class="who"><strong>Rhys Calder</strong><small>Lorem Ipsum</small></div><span class="status">Online</span></li>
  <li><div class="photo" role="img" aria-label="User profile photo"></div><div class="who"><strong>Rhys Calder</strong><small>Lorem Ipsum</small></div><span class="status">Online</span></li>
  <li><div class="photo" role="img" aria-label="User profile photo"></div><div class="who"><strong>Rhys Calder</strong><small>Lorem Ipsum</small></div><span class="status">Online</span></li>
</ul>
</body>
</html>
```